Brochure Redesign

We need a new, adapted, design for our Brochure. A few weeks ago we've setup a new Homepage design and for now we want to adapt our old Brochure to the new design.

Requirements:
-) Place the 3 products quite prominent
-) Place also our add ons
-) Use the Keyvisuals you can find on the Homepage

New Homepage: www.rufkontor-werk.at
Old Folder version - see attached

Requirements
Must have
• Logo and basic design from Homepage

```html
<!DOCTYPE html>
<html lang="de">
<head>
<meta charset="utf-8">
<title>Rufkontor-Werk Faltblatt</title>
<link href="https://fonts.googleapis.com/css2?family=Arimo:wght@400;700&display=swap" rel="stylesheet">
<style>
:root{
  --maroon:#7d1a22;
  --maroon-dark:#5e0f16;
  --orange:#f08a1c;
  --yellow:#f5c417;
  --yellow-light:#f8d84a;
  --grey-bg:#ececec;
  --card:#e4e4e6;
  --text:#444;
  --white:#fff;
  --stage:#dcdcdc;
}
*{box-sizing:border-box;margin:0;padding:0}
html,body{width:1200px;height:1080px;overflow:hidden}
body{background:var(--stage);font-family:"Arimo",Arial,sans-serif;color:var(--text);position:relative}
.brochure{position:absolute;left:60px;top:160px;width:1080px;height:760px;display:flex;box-shadow:0 10px 30px rgba(0,0,0,.18)}
.panel{position:relative;width:360px;height:760px;background:var(--white);overflow:hidden}
.abs{position:absolute}
svg.bg{position:absolute;left:0;top:0}

/* left */
.intro-title{left:22px;top:22px;color:var(--white);font-weight:700;font-size:17px;line-height:21px}
.benefits{left:22px;top:72px;list-style:none}
.benefits li{display:flex;align-items:center;gap:9px;color:var(--white);font-size:12px;height:22.5px}
.benefits li.hl{color:var(--yellow);font-weight:700}
.tick{width:14px;height:14px;flex:none}
.step{left:14px;width:330px;height:120px}
.step-photo{position:absolute;left:0;top:0;width:72px;height:72px;border-radius:50%;background:radial-gradient(circle at 40% 40%,#f4efe6,#bba98f);z-index:2}
.step-card{position:absolute;left:20px;top:30px;width:310px;height:90px;background:var(--card);border-radius:0 0 0 14px}
.step-num{position:absolute;left:0;top:0;width:30px;height:90px;background:var(--maroon);color:var(--white);font-size:28px;font-weight:700;display:flex;align-items:flex-end;justify-content:center;padding-bottom:10px;border-radius:0 0 0 14px}
.step-tab{position:absolute;right:0;top:-6px;width:140px;height:22px;background:linear-gradient(90deg,rgba(245,196,23,0),var(--yellow) 35%);color:var(--maroon);font-weight:700;font-size:12px;text-align:right;padding:4px 8px 0 0}
.step-text{position:absolute;left:60px;right:12px;top:26px;font-size:9.5px;line-height:12px;color:#666}
.step-text.r{text-align:right}
.step-corner{position:absolute;right:0;bottom:0;width:0;height:0;border-left:16px solid transparent;border-bottom:16px solid var(--maroon)}

/* middle */
.bubble{left:48px;top:22px;width:172px;height:112px}
.bubble-text{left:76px;top:58px;width:118px;color:var(--maroon-dark)}
.bubble-text h3{font-size:14px;font-weight:700;margin-bottom:3px}
.bubble-text p{font-size:9px;line-height:11px}
.store-badge{left:50px;top:172px;width:100px;height:32px;background:#111;border:1px solid #999;border-radius:5px}
.os-mark{left:165px;top:166px;width:40px;height:40px;border-radius:50%;background:#8bbf3a}
.phone{left:232px;top:108px;width:64px;height:112px;border-radius:10px;background:linear-gradient(160deg,#3a3a3a,#111)}
.phone-screen{position:absolute;left:6px;top:12px;right:6px;bottom:14px;background:linear-gradient(#fff,#f0d6d6);border-radius:2px}
.adv-title{left:42px;top:248px;color:var(--maroon);font-size:25px;font-weight:700}
.adv-sub{left:42px;top:278px;color:var(--maroon);font-size:17px;font-weight:700}
.adv-list{left:42px;top:300px;list-style:none;font-size:11px;line-height:13px;color:var(--maroon-dark)}
.test-title{left:42px;top:425px;color:var(--maroon);font-size:17px;font-weight:700}
.test-text{left:42px;top:452px;width:258px;font-size:10.5px;line-height:13px;color:#555}
.test-text strong{color:var(--maroon)}
.cost-head{left:42px;top:570px;width:240px;height:20px;background:#d6d6d6;color:var(--maroon);font-weight:700;font-size:12px;padding:3px 0 0 9px}
.cost-table{left:50px;top:598px;width:230px;font-size:9.5px;color:#666;border-collapse:collapse}
.cost-table td{line-height:11.5px;padding:0}
.cost-table td.v{text-align:left;width:45px}
.cost-table tr.sum td{padding-top:12px}

/* right */
.addon-head{left:0;top:0;width:360px;height:48px;background:var(--maroon);color:var(--white);font-size:19px;font-weight:700;padding:13px 0 0 118px}
.addon{left:0;width:360px;text-align:center}
.addon-icon{width:72px;height:72px;border-radius:50%;margin:0 auto;background:radial-gradient(circle at 40% 35%,var(--yellow-light),#e6a90c)}
.price{display:inline-block;margin-top:8px;background:var(--yellow);color:var(--maroon-dark);font-weight:700;font-size:13px;padding:3px 6px;border-radius:3px}
.addon h4{color:var(--maroon-dark);font-size:14px;font-weight:700;margin-top:5px}
.addon p{width:250px;margin:3px auto 0;font-size:9.5px;line-height:11.5px;text-align:justify;color:#555}
.tags{display:flex;justify-content:center;gap:8px;margin-top:10px}
.tag{background:var(--yellow);border-radius:3px;padding:3px 6px;color:var(--maroon-dark);text-align:center}
.tag small{display:block;font-size:7px;line-height:8px}
.tag b{font-size:13px}
</style>
</head>
<body>
<main class="brochure">

  <!-- Panel 1 -->
  <section class="panel panel-services">
    <svg class="bg" width="360" height="340" viewBox="0 0 360 340" aria-hidden="true">
      <path d="M0 0H360V200C320 300 200 320 0 300Z" fill="#f08a1c"/>
      <path d="M0 0H360V180C310 270 190 290 0 280Z" fill="#7d1a22"/>
    </svg>
    <h2 class="abs intro-title">DAS BIETET IHNEN<br>RUFKONTOR-WERK.AT</h2>
    <ul class="abs benefits">
      <li><svg class="tick" viewBox="0 0 14 14"><circle cx="7" cy="7" r="7" fill="#f5c417"/><path d="M3.5 7.2l2.3 2.3 4.5-5" stroke="#7d1a22" stroke-width="2" fill="none"/></svg>Ihr Unternehmen ist 24h / 365 Tage erreichbar</li>
      <li><svg class="tick" viewBox="0 0 14 14"><circle cx="7" cy="7" r="7" fill="#f5c417"/><path d="M3.5 7.2l2.3 2.3 4.5-5" stroke="#7d1a22" stroke-width="2" fill="none"/></svg>Alle Daten online abruf- und änderbar</li>
      <li><svg class="tick" viewBox="0 0 14 14"><circle cx="7" cy="7" r="7" fill="#f5c417"/><path d="M3.5 7.2l2.3 2.3 4.5-5" stroke="#7d1a22" stroke-width="2" fill="none"/></svg>Persönliche Anrufentgegennahme</li>
      <li><svg class="tick" viewBox="0 0 14 14"><circle cx="7" cy="7" r="7" fill="#f5c417"/><path d="M3.5 7.2l2.3 2.3 4.5-5" stroke="#7d1a22" stroke-width="2" fill="none"/></svg>Individueller Meldetext</li>
      <li><svg class="tick" viewBox="0 0 14 14"><circle cx="7" cy="7" r="7" fill="#f5c417"/><path d="M3.5 7.2l2.3 2.3 4.5-5" stroke="#7d1a22" stroke-width="2" fill="none"/></svg>Gesprächsnotizen jederzeit online abrufbar</li>
      <li><svg class="tick" viewBox="0 0 14 14"><circle cx="7" cy="7" r="7" fill="#f5c417"/><path d="M3.5 7.2l2.3 2.3 4.5-5" stroke="#7d1a22" stroke-width="2" fill="none"/></svg>Im ersten Monat keine Grundgebühr</li>
      <li class="hl"><svg class="tick" viewBox="0 0 14 14"><circle cx="7" cy="7" r="7" fill="#f5c417"/><path d="M3.5 7.2l2.3 2.3 4.5-5" stroke="#7d1a22" stroke-width="2" fill="none"/></svg>Keine Kündigungsfrist</li>
      <li class="hl"><svg class="tick" viewBox="0 0 14 14"><circle cx="7" cy="7" r="7" fill="#f5c417"/><path d="M3.5 7.2l2.3 2.3 4.5-5" stroke="#7d1a22" stroke-width="2" fill="none"/></svg>Keine Einrichtungskosten</li>
      <li class="hl"><svg class="tick" viewBox="0 0 14 14"><circle cx="7" cy="7" r="7" fill="#f5c417"/><path d="M3.5 7.2l2.3 2.3 4.5-5" stroke="#7d1a22" stroke-width="2" fill="none"/></svg>Keine Mindestvertragslaufzeit</li>
    </ul>

    <div class="abs step" style="top:318px">
      <div class="step-photo" role="img" aria-label="Foto: Hände auf einer Tastatur"></div>
      <div class="step-card">
        <div class="step-num">1</div>
        <div class="step-tab">Dateneingabe</div>
        <p class="step-text r">Das Service-Paket "Rund um die Uhr" steht Ihnen 24 Stunden am Tag, 365 Tage im Jahr zur Verfügung. Die Servicezeiten umfassen damit auch Sonn- und Feiertage.</p>
        <div class="step-corner"></div>
      </div>
    </div>
    <div class="abs step" style="top:460px">
      <div class="step-photo" role="img" aria-label="Foto: Hand hält ein Mobiltelefon"></div>
      <div class="step-card">
        <div class="step-num">2</div>
        <div class="step-tab">Rufumleitung</div>
        <p class="step-text">Sofort nach erfolgreicher Buchung erhalten Sie Ihre Zielrufnummer. Leiten Sie Ihr Telefon einfach auf diese Nummer um (Hilfe).</p>
        <div class="step-corner"></div>
      </div>
    </div>
    <div class="abs step" style="top:602px">
      <div class="step-photo" role="img" aria-label="Foto: Mitarbeiterin mit Headset"></div>
      <div class="step-card">
        <div class="step-num">3</div>
        <div class="step-tab">Ihr Sekretariat</div>
        <p class="step-text">Ihr neues Sekretariat ist nun aktiv. Sie und all Ihre Mitarbeiter werden in Echtzeit, individuell über eingehende Anrufe informiert.</p>
        <div class="step-corner"></div>
      </div>
    </div>
  </section>

  <!-- Panel 2 -->
  <section class="panel panel-offer" style="background:var(--grey-bg)">
    <svg class="bg" width="360" height="395" viewBox="0 0 360 395" aria-hidden="true">
      <defs>
        <linearGradient id="warm" x1="0" y1="0" x2="0" y2="1">
          <stop offset="0" stop-color="#f08a1c"/><stop offset="1" stop-color="#e9a514"/>
        </linearGradient>
        <linearGradient id="sun" x1="0" y1="0" x2="0" y2="1">
          <stop offset="0" stop-color="#f7cf2a"/><stop offset="1" stop-color="#f0b50f"/>
        </linearGradient>
      </defs>
      <rect width="360" height="395" fill="#ececec"/>
      <path d="M0 120C90 60 230 40 330 130L360 160V395H0Z" fill="url(#warm)"/>
      <path d="M0 170C110 100 260 110 320 230L340 395H0Z" fill="url(#sun)"/>
    </svg>
    <svg class="abs bubble" viewBox="0 0 172 112" aria-hidden="true">
      <path d="M4 4L150 8Q160 9 160 20L162 84Q162 94 152 94L120 96L150 110L100 96L20 96Q10 96 10 86Z" fill="#f08a1c" stroke="#7d1a22" stroke-width="4" stroke-linejoin="round"/>
    </svg>
    <div class="abs bubble-text">
      <h3>Kostenlose App</h3>
      <p>Laden Sie jetzt die kostenlose rufkontor-werk App direkt online herunter.</p>
    </div>
    <div class="abs store-badge" aria-hidden="true"></div>
    <div class="abs os-mark" aria-hidden="true"></div>
    <div class="abs phone" role="img" aria-label="Illustration: Smartphone mit geöffneter App"><div class="phone-screen"></div></div>

    <h2 class="abs adv-title">Ihre Vorteile</h2>
    <p class="abs adv-sub">Einfach, Immer, Erreichbar</p>
    <ul class="abs adv-list">
      <li>- Individueller Meldetext</li>
      <li>- Beliebig viele Mitarbeiter</li>
      <li>- 24h Erreichbarkeit</li>
      <li>- Ohne Mindestvertragslaufzeit</li>
      <li>- Keine versteckten Callminuten</li>
    </ul>

    <h2 class="abs test-title">24h - GRATIS -TEST</h2>
    <p class="abs test-text"><strong>Jederzeit unverbindlich einen Tag kostenlos auf rufkontor-werk.at testen.</strong> Einfach Meldetext sowie Firmen- und Personendaten eingeben, schon wird der Testzugang vollautomatisch eingerichtet. Sobald Sie sich von den Vorteilen Ihres neuen Sekretariats überzeugt haben, können Sie innerhalb der 24-stündigen Testphase gleich online buchen, indem Sie Ihre Zahlungsdaten ergänzen.</p>
    <div class="abs cost-head">KOSTEN</div>
    <table class="abs cost-table">
      <tr><td>Monatl. Grundgebühr</td><td class="v"></td></tr>
      <tr><td>Service-Paket "Bürozeiten"</td><td class="v">€ 29,00</td></tr>
      <tr><td>50 Anrufe pro Monat</td><td class="v">€ 99,50</td></tr>
      <tr><td>11 Sofortbenachrichtigungen per SMS</td><td class="v">€ 3,30</td></tr>
      <tr><td>Telefonspesen</td><td class="v">€ 4,70</td></tr>
      <tr class="sum"><td>Gesamtaufwand</td><td class="v">€ 136,50</td></tr>
    </table>
  </section>

  <!-- Panel 3 -->
  <section class="panel panel-addons">
    <h2 class="abs addon-head">ADD ON'S</h2>
    <div class="abs addon" style="top:70px">
      <div class="addon-icon" role="img" aria-label="Illustration: Buch mit Lupe"></div>
      <span class="price">€ 19,-</span>
      <h4>Online Wissensdatenbank</h4>
      <p>Our online knowledge base forms the basis for the professional storage of your information and serves as an interface between your experts, call center and customer. Structured information processing allows searches by keyword, category and / or free text.</p>
    </div>
    <div class="abs addon" style="top:292px">
      <div class="addon-icon" role="img" aria-label="Illustration: Kalenderblatt"></div>
      <span class="price">€ 29,-</span>
      <h4>Online Terminkalender</h4>
      <p>Sämtliche Anforderungen wie Terminlängen, Kategorien, Zeitfenster, etc. werden individuell an Ihre Bedürfnisse angepasst und ermöglichen ortsunabhängig alle Termine zu verwalten. Eine Tages- oder Wochenansicht bietet zusätzlich einen strukturierten Gesamtüberblick aller Termine.</p>
    </div>
    <div class="abs addon" style="top:526px">
      <div class="addon-icon" role="img" aria-label="Illustration: Studiomikrofon"></div>
      <div class="tags">
        <div class="tag"><small>Neutrale<br>Bandansage</small><b>€ 4,90</b></div>
        <div class="tag"><small>Personalisierte<br>Bandansage</small><b>€ 7,90</b></div>
        <div class="tag"><small>Anrufbeantworterfunktion</small><b>€ 9,90</b></div>
      </div>
      <h4>Tonbänder &amp; Co</h4>
      <p>Sie haben die Möglichkeit mit neutralen und individuellen Bandansagen oder einer Anrufbeantworterfunktion Ihren Kunden noch mehr Service zu bieten.</p>
    </div>
  </section>

</main>
</body>
</html>
```